Chimney Service company needs new business card design

We need a updated business card with our new logo added. We provide a full range of chimney services throughout Vermont and New Hampshire. The business card will be one sided and color. Attached is our current business card another document showing all the information we would like on the card.
We dont like a lot of flashy colors.... here is a link to our website to get an idea of our branding www.flueguardianvt.example

Target Market(s)

homeowners

Industry/Entity Type

Business

Contact Information for Business Card

See attached sheet for content.

Font styles to use
Serif
Sans Serif

Requirements
Must have
• all information provided on separate sheet
Should not have
• Additional information that may clogg up design

```html
<!DOCTYPE html>
<html lang="en">
<head>
<meta charset="utf-8">
<title>Flue Guardian – Business Card</title>
<link rel="stylesheet" href="https://fonts.googleapis.com/css2?family=Marcellus&family=Roboto:wght@400;700&family=Open+Sans:wght@400&display=swap">
<style>
  :root {
    --page-bg: #bdbdbd;
    --card-bg: #f1f1f1;
    --brand-red: #8e0a0a;
    --brand-red-mid: #a3201e;
    --charcoal: #2e2e2e;
    --text-dark: #3a3a3a;
    --rule-grey: #9a9a9a;
    --icon-tint: #ecd7d5;
  }
  * { box-sizing: border-box; margin: 0; padding: 0; }
  html, body { width: 1200px; height: 576px; overflow: hidden; }
  body { background: var(--page-bg); position: relative; font-family: "Roboto", Arial, sans-serif; }

  .card {
    position: absolute; top: 138px; width: 484px; height: 294px;
    background: var(--card-bg); border-radius: 12px; overflow: hidden;
  }
  .card--front { left: 82px; }
  .card--back { left: 602px; width: 480px; height: 292px; }

  /* Company name */
  .company-name {
    position: absolute; left: 0; right: 0; text-align: center;
    font-family: "Marcellus", Georgia, serif; letter-spacing: 0.5px; line-height: 1;
  }
  .company-name--front { top: 56px; font-size: 27px; color: #fff; }
  .company-name--back { top: 74px; font-size: 34px; color: var(--charcoal); }

  /* Front */
  .front-band { position: absolute; left: 0; top: 0; width: 484px; height: 150px; }

  .services { position: absolute; left: 0; top: 160px; width: 484px; display: flex; list-style: none; }
  .service { flex: 1; display: flex; flex-direction: column; align-items: center; position: relative; }
  .service + .service::before {
    content: ""; position: absolute; left: 0; top: 4px; height: 72px; width: 1px; background: var(--brand-red-mid); opacity: .6;
  }
  .service__icon { width: 38px; height: 44px; background: var(--icon-tint); border-radius: 3px; }
  .service__label { margin-top: 14px; font-size: 11.5px; line-height: 1.25; color: var(--text-dark); text-align: center; }

  .front-web {
    position: absolute; left: 86px; right: 86px; top: 266px; display: flex; align-items: center; gap: 10px;
    font-size: 11.5px; color: var(--text-dark); white-space: nowrap;
  }
  .front-web::before, .front-web::after { content: ""; flex: 1; height: 1.5px; background: var(--brand-red-mid); }
  .accent { color: var(--brand-red); }

  /* Back */
  .region { position: absolute; left: 50px; top: 170px; width: 164px; text-align: center; }
  .region__title { font-weight: 700; font-size: 17.5px; line-height: 1.15; color: var(--charcoal); }
  .region__since { display: flex; align-items: center; gap: 6px; font-size: 9px; color: var(--text-dark); margin-top: 4px; letter-spacing: .5px; }
  .region__since::before, .region__since::after { content: ""; flex: 1; height: 1.5px; background: var(--brand-red-mid); }

  .divider { position: absolute; left: 234px; top: 165px; width: 1px; height: 68px; background: var(--brand-red-mid); }

  .contact { position: absolute; left: 256px; top: 170px; list-style: none; }
  .contact li { display: flex; align-items: center; gap: 10px; font-size: 12px; color: var(--text-dark); height: 19.5px; }
  .contact svg { width: 11px; height: 11px; fill: var(--brand-red); flex: none; }

  .back-rule { position: absolute; left: 22px; right: 22px; top: 259px; height: 1px; background: var(--rule-grey); }
  .back-footer {
    position: absolute; left: 0; right: 0; top: 267px; text-align: center;
    font-family: "Open Sans", Arial, sans-serif; font-size: 11px; color: var(--text-dark);
  }
  .back-footer .sep { color: var(--brand-red); margin: 0 12px; }
</style>
</head>
<body>

<section class="card card--front" aria-label="Card front">
  <svg class="front-band" viewBox="0 0 484 150" aria-hidden="true">
    <path d="M0 0 H484 V108 C400 140 300 146 230 140 C140 132 60 110 0 100 Z" fill="#2a2a2a"/>
    <path d="M0 0 H484 V100 C400 134 300 140 230 133 C140 125 60 104 0 94 Z" fill="#8e0a0a"/>
  </svg>

  <p class="company-name company-name--front">FLUE GUARDIAN</p>

  <ul class="services">
    <li class="service"><span class="service__icon" role="img" aria-label="Masonry chimney icon"></span><span class="service__label">Full Masonry<br>Services</span></li>
    <li class="service"><span class="service__icon" role="img" aria-label="Brick restoration icon"></span><span class="service__label">Historic Chimney<br>Restoration</span></li>
    <li class="service"><span class="service__icon" role="img" aria-label="Steel liner icon"></span><span class="service__label">Stainless<br>Steel Liners</span></li>
    <li class="service"><span class="service__icon" role="img" aria-label="Bricks and trowel icon"></span><span class="service__label">New Chimney<br>Installations</span></li>
    <li class="service"><span class="service__icon" role="img" aria-label="Chimney sweep brush icon"></span><span class="service__label">Fully Certified<br>Chimney sweeps</span></li>
  </ul>

  <p class="front-web"><span>www.<span class="accent">flueguardianvt</span>.example</span></p>
</section>

<section class="card card--back" aria-label="Card back">
  <p class="company-name company-name--back">FLUE GUARDIAN</p>

  <div class="region">
    <p class="region__title">SERVING VT AND<br>NEW HAMPSHIRE</p>
    <p class="region__since">SINCE 1989</p>
  </div>

  <span class="divider"></span>

  <ul class="contact">
    <li>
      <svg viewBox="0 0 12 12" aria-hidden="true"><path d="M1 4 C1 2 3 1.5 6 1.5 S11 2 11 4 L9 5 L8.3 3.8 H3.7 L3 5 Z M2.5 6 H9.5 L10.5 10.5 H1.5 Z"/></svg>
      <span>802-555-0147</span>
    </li>
    <li>
      <svg viewBox="0 0 12 12" aria-hidden="true"><path d="M1 2.5 H11 V9.5 H1 Z"/><path d="M1.5 3 L6 6.5 L10.5 3" stroke="#f1f1f1" stroke-width="1" fill="none"/></svg>
      <span>info@flueguardianvt.example</span>
    </li>
    <li>
      <svg viewBox="0 0 12 12" aria-hidden="true"><circle cx="6" cy="6" r="5"/><path d="M1 6 H11 M6 1 C3.5 3.5 3.5 8.5 6 11 M6 1 C8.5 3.5 8.5 8.5 6 11" stroke="#f1f1f1" stroke-width=".8" fill="none"/></svg>
      <span>www.<span class="accent">flueguardianvt</span>.example</span>
    </li>
  </ul>

  <span class="back-rule"></span>
  <p class="back-footer">Fully Insured – Free Estimates<span class="sep">|</span>Family Owned &amp; Operated</p>
</section>

</body>
</html>
```